Corporate Travel Technology Company needs new Business Card design

We need a new business card design to reflect our re-branded company. Our company is called tolvEn (pronounced tolvenn) and we provide Business Intelligence and mobile travel management solutions for the corporate travel industry. Our multinational customers use our solutions to manage large travel budgets and frequent travellers, as well as to save money and reduce risk. We'd like to see designs that use the blue and green palette as well as our corporate logo (attached below). The design should communicate innovation, insight, forward thinking, contemporary, trusted.

Target Market(s)

Large multinational corporates and Travel Agencies.

Industry/Entity Type

Business

Contact Information for Business Card

Rosalind Mercer
Chief Executive
tolvEn
Phone number - +61 (0)2 8134 2907
Email address - rosalind.mercer@tolven-example.com
Mobile number - +61 (0)438 516 702
www.tolven-example.com

Font styles to use
Other font styles liked:
• Please use font as close to corporate logo as possible

Colors
0255a3
0393ce
00a990
33b8a4
33a6d7
3176b5

Requirements
Must have
• Please include the words;
• Mobile Travel Management
• Accelerating Travel Business Insights
• Use corporate logo - although icon can be stylised if needed

```html
<!DOCTYPE html>
<html lang="en">
<head>
<meta charset="utf-8">
<title>tolvEn — Business Card</title>
<link rel="stylesheet" href="https://fonts.googleapis.com/css2?family=Open+Sans:wght@400;600&family=Roboto:wght@400;700&display=swap">
<style>
  :root {
    --stage: #ffffff;
    --mat: #d1d3d4;
    --card: #f1f1f1;
    --teal: #13a89e;
    --ink: #3a3a3a;
    --brand-ink: #455b59;
    --sky: #33a6d7;
    --white: #ffffff;
  }
  * { margin: 0; padding: 0; box-sizing: border-box; }
  html, body {
    width: 1200px; height: 440px; overflow: hidden;
    background: var(--stage);
  }
  .mat {
    position: absolute; left: 17px; top: 40px;
    width: 1172px; height: 360px;
    background: var(--mat);
  }
  .card {
    position: absolute; top: 50px;
    width: 552px; height: 331px;
    background: var(--card);
    overflow: hidden;
    font-family: "Open Sans", sans-serif;
  }
  .card--front { left: 35px; }
  .card--back { left: 622px; }
  .block {
    position: absolute; background: var(--teal);
  }
  .card--front .block--top { left: 145px; top: 0; width: 252px; height: 69px; }
  .card--front .block--bottom {
    left: 145px; top: 237px; width: 252px; height: 94px;
    display: flex; flex-direction: column; justify-content: center; align-items: center;
    font-family: "Roboto", sans-serif; font-size: 13.5px; line-height: 1.35;
    color: var(--white); text-align: center;
  }
  .card--back .block--top { left: 64px; top: 0; width: 149px; height: 108px; }
  .card--back .block--bottom { left: 64px; top: 208px; width: 149px; height: 123px; }

  .brand {
    position: absolute; display: flex; align-items: center;
    font-family: "Open Sans", sans-serif; font-weight: 400;
    color: var(--brand-ink); letter-spacing: -1px;
  }
  .brand__dot { border-radius: 50%; background: var(--sky); flex: none; }
  .card--front .brand { left: 0; width: 552px; top: 110px; justify-content: center; font-size: 78px; gap: 12px; }
  .card--front .brand__dot { width: 26px; height: 26px; }
  .card--back .brand { left: 0; width: 278px; top: 148px; justify-content: center; font-size: 42px; gap: 7px; }
  .card--back .brand__dot { width: 15px; height: 15px; }

  .person {
    position: absolute; right: 32px; top: 50px; text-align: right;
    font-family: "Roboto", sans-serif;
  }
  .person__name { font-size: 25px; font-weight: 700; color: var(--ink); letter-spacing: 0.2px; line-height: 1.1; }
  .person__name .surname { color: var(--teal); }
  .person__role { font-size: 18px; font-weight: 400; color: var(--ink); margin-top: 2px; }

  .contact {
    position: absolute; right: 32px; display: flex; align-items: center; gap: 18px;
    font-size: 13.5px; color: var(--ink); text-align: right; line-height: 1.25;
  }
  .contact--phone { top: 157px; }
  .contact--email { top: 216px; }
  .contact--web { top: 272px; }
  .contact__icon { width: 30px; height: 30px; flex: none; }
</style>
</head>
<body>
  <div class="mat"></div>

  <section class="card card--front" aria-label="Card front">
    <div class="block block--top"></div>
    <div class="brand"><span class="brand__dot"></span><span class="brand__name">tolvEn</span></div>
    <div class="block block--bottom">
      <p class="tagline">Mobile Travel Management</p>
      <p class="tagline">Accelerating Travel Business Insights</p>
    </div>
  </section>

  <section class="card card--back" aria-label="Card back">
    <div class="block block--top"></div>
    <div class="brand"><span class="brand__dot"></span><span class="brand__name">tolvEn</span></div>
    <div class="block block--bottom"></div>

    <div class="person">
      <p class="person__name">ROSALIND<span class="surname">MERCER</span></p>
      <p class="person__role">Chief Executive</p>
    </div>

    <div class="contact contact--phone">
      <p>+61 (0)2 8134 2907<br>+61 (0)438 516 702</p>
      <svg class="contact__icon" viewBox="0 0 24 24" aria-hidden="true">
        <path fill="#13a89e" d="M6.6 10.8a15.1 15.1 0 0 0 6.6 6.6l2.2-2.2c.3-.3.7-.4 1-.2 1.1.4 2.3.6 3.6.6.6 0 1 .4 1 1V20c0 .6-.4 1-1 1A17 17 0 0 1 3 4c0-.6.4-1 1-1h3.5c.6 0 1 .4 1 1 0 1.3.2 2.5.6 3.6.1.3 0 .7-.2 1z"/>
      </svg>
    </div>

    <div class="contact contact--email">
      <p>rosalind.mercer@tolven-example.com</p>
      <svg class="contact__icon" viewBox="0 0 24 24" aria-hidden="true">
        <rect x="2" y="5" width="20" height="14" fill="#13a89e"/>
        <path d="M2.5 5.5 12 13l9.5-7.5M2.5 18.5l7-6.5M21.5 18.5l-7-6.5" fill="none" stroke="#f1f1f1" stroke-width="1.3"/>
      </svg>
    </div>

    <div class="contact contact--web">
      <p>www.tolven-example.com</p>
      <svg class="contact__icon" viewBox="0 0 24 24" aria-hidden="true">
        <g fill="none" stroke="#13a89e" stroke-width="1.8">
          <circle cx="12" cy="12" r="9.5"/>
          <ellipse cx="12" cy="12" rx="4.2" ry="9.5"/>
          <path d="M2.5 12h19M4 7h16M4 17h16"/>
        </g>
      </svg>
    </div>
  </section>
</body>
</html>
```